Letterhead for Business Law Firm

We need a letter head for our firm based on the design we have settled on and it is attached. Our clients are small and large businesses around the world, and our letterhead is used typically for formal legal purposes such as demand letters (accusing the recipient of doing bad things) or responding to demand letters. It may also be sent to regulators and other government agencies. So this needs to be tasteful, but a little edgy as well - we try to convey that we are a firm that is different - businesses and investors come to us for creative, quick advice, typically in high stress circumstances, and for our ability to work through high conflict situations, and rapid paced engagements.

Target Market(s)

Lawyers, business executives, investors, government regulators who may receive letters from this firm on behalf of its clients.

Industry/Entity Type

Business

Requirements
Must have
• The design and the firm's contact information:
• Thornwell Law Firm, P.C.
• 1876 NE 57th Ave
• Portland, OR 97213
• phone: 971 555 0147
• fax: 971 555 0182
• in what placement and how depicted (e.g. a phone icon instead of the word "phone") I leave to your creative ideas.
Nice to have
• design and information can be placed at the top, bottom and/or sides of the letter, and the design should be for a standard letter size paper - and can have a separate design for the second page.

```html
<!DOCTYPE html>
<html lang="en">
<head>
<meta charset="utf-8">
<title>Thornwell Letterhead</title>
<link rel="stylesheet" href="https://fonts.googleapis.com/css2?family=PT+Sans:wght@400&display=swap">
<style>
  :root {
    --backdrop: #e6e6e4;
    --paper: #ffffff;
    --ink: #1b1718;
    --text: #2c2c2c;
    --teal: #4a7f86;
    --rule: #b9b9b9;
    --footer-text: #ffffff;
  }
  * { margin: 0; padding: 0; box-sizing: border-box; }
  html, body {
    width: 1019px;
    height: 1200px;
    overflow: hidden;
    background: var(--backdrop);
    font-family: "PT Sans", Arial, sans-serif;
  }
  .letterhead {
    position: absolute;
    left: 45px;
    top: 0;
    width: 928px;
    height: 1200px;
    background: var(--paper);
    overflow: hidden;
  }
  .brand {
    position: absolute;
    left: 69px;
    top: 54px;
    height: 79px;
    display: flex;
    align-items: center;
    gap: 18px;
  }
  .brand-square {
    width: 46px;
    height: 46px;
    background: var(--ink);
  }
  .brand-name {
    font-size: 44px;
    font-weight: 400;
    letter-spacing: 9px;
    color: var(--ink);
    line-height: 1;
  }
  .contact {
    position: absolute;
    left: 734px;
    top: 54px;
    height: 80px;
    border-left: 1px solid var(--rule);
    padding-left: 14px;
    padding-top: 3px;
    list-style: none;
  }
  .contact-item {
    display: flex;
    align-items: center;
    gap: 5px;
    font-size: 14px;
    line-height: 19.2px;
    color: var(--text);
  }
  .contact-icon { width: 10px; height: 10px; flex: none; }
  .footer-wave {
    position: absolute;
    left: 0;
    bottom: 0;
    width: 928px;
    height: 135px;
    display: block;
  }
  .address {
    position: absolute;
    left: 79px;
    top: 1138px;
    font-size: 14px;
    line-height: 23px;
    color: var(--footer-text);
    font-style: normal;
  }
</style>
</head>
<body>
<main class="letterhead">
  <header>
    <div class="brand">
      <span class="brand-square"></span>
      <span class="brand-name">THORNWELL</span>
    </div>
    <ul class="contact">
      <li class="contact-item">
        <svg class="contact-icon" viewBox="0 0 10 10" aria-hidden="true"><path d="M2 1 L4 1 L4.6 3 L3.4 3.8 C4 5.2 4.8 6 6.2 6.6 L7 5.4 L9 6 L9 8 C5 8.5 1.5 5 2 1 Z" fill="var(--teal)"/></svg>
        123-456-0789
      </li>
      <li class="contact-item">
        <svg class="contact-icon" viewBox="0 0 10 10" aria-hidden="true"><rect x="3" y="1" width="4" height="3" fill="var(--teal)"/><rect x="1" y="4.5" width="8" height="4.5" rx="1" fill="var(--teal)"/></svg>
        123-456-0789
      </li>
      <li class="contact-item">
        <svg class="contact-icon" viewBox="0 0 10 10" aria-hidden="true"><rect x="1" y="2.5" width="8" height="5.5" fill="var(--teal)"/><path d="M1 2.5 L5 5.5 L9 2.5" stroke="#fff" stroke-width="1" fill="none"/></svg>
        info@thornwell.com
      </li>
      <li class="contact-item">
        <svg class="contact-icon" viewBox="0 0 10 10" aria-hidden="true"><circle cx="5" cy="5" r="4" fill="none" stroke="var(--teal)" stroke-width="1"/><path d="M1 5 H9 M5 1 V9 M2 3 H8 M2 7 H8" stroke="var(--teal)" stroke-width="0.7"/></svg>
        www.thornwell.com
      </li>
    </ul>
  </header>

  <svg class="footer-wave" viewBox="0 1180 1028 149" preserveAspectRatio="none" aria-hidden="true">
    <path d="M0,1247 C140,1222 300,1222 470,1252 C650,1285 850,1322 1028,1316 L1028,1329 L0,1329 Z" fill="var(--ink)"/>
    <path d="M0,1236 C130,1206 320,1206 440,1248 C320,1218 140,1220 0,1243 Z" fill="var(--ink)"/>
    <path d="M120,1213 C350,1200 560,1250 760,1290 C880,1310 980,1305 1028,1297" fill="none" stroke="#4a4a4a" stroke-width="2"/>
    <path d="M560,1253 C700,1285 860,1300 1028,1265 L1028,1283 C880,1300 720,1290 560,1253 Z" fill="var(--teal)"/>
    <path d="M700,1292 C850,1316 960,1311 1028,1303" fill="none" stroke="#4a4a4a" stroke-width="1.5"/>
  </svg>

  <address class="address">
    00, complex name<br>
    City, state
  </address>
</main>
</body>
</html>
```